Construction company business card

One side to be the logo with the company name, The other side I would like: (Tomas verbick) Project manager 41 barrow crescent hallam 52917306224783(03) 9703 2428Info@gudeljgroup.comAnd then maybe a couple dot points saying what we do:Construction (commercial & industrial) Civil construction

Anything else please contact me!
Maybe curved st one edge of the card

Target Market(s)

Older clientele

Industry/Entity Type

Construction Company

Contact Information for Business Card

Read above

Colors
3277b5
1b1b1b
9d9d9d

Requirements
Must have
• Use my logo on one side
Nice to have
• Read above
Should not have
• Read above

```html
<!DOCTYPE html>
<html lang="en">
<head>
<meta charset="utf-8">
<title>Ridgeline Construction – Business Card</title>
<link rel="stylesheet" href="https://fonts.googleapis.com/css2?family=Open+Sans:ital,wght@0,400;0,700;1,400&display=swap">
<style>
  :root {
    --brand-blue: #0f59a7;
    --ink: #1b1b1b;
    --ink-soft: #4a4a4a;
    --muted: #9d9d9d;
    --paper: #ffffff;
    --backdrop: #e9eaec;
  }
  * { box-sizing: border-box; margin: 0; padding: 0; }
  html, body { width: 1200px; height: 900px; overflow: hidden; }
  body {
    background: var(--backdrop);
    font-family: "Open Sans", Arial, sans-serif;
    position: relative;
  }
  .card {
    position: absolute;
    width: 620px;
    height: 354px;
    box-shadow: 0 10px 28px rgba(0,0,0,0.14);
  }
  .card-front {
    left: 60px; top: 70px;
    background: var(--brand-blue);
    display: flex; align-items: center; justify-content: center;
  }
  .card-back {
    left: 520px; top: 476px;
    background: var(--paper);
  }
  .wordmark {
    display: flex; align-items: center; gap: 16px;
    font-weight: 700;
    letter-spacing: 0.06em;
    text-transform: uppercase;
  }
  .wordmark-dot {
    width: 46px; height: 46px; border-radius: 50%;
    flex: none;
  }
  .wordmark-name { font-size: 30px; line-height: 1.1; }
  .card-front .wordmark { color: var(--paper); }
  .card-front .wordmark-dot { background: var(--paper); }
  .card-back .wordmark {
    position: absolute; right: 36px; top: 62px;
    color: var(--brand-blue);
    gap: 10px;
  }
  .card-back .wordmark-dot { width: 30px; height: 30px; background: var(--brand-blue); }
  .card-back .wordmark-name { font-size: 19px; }

  .contact {
    position: absolute; left: 0; top: 104px;
    padding-left: 46px;
    color: var(--ink-soft);
    font-size: 14px;
    line-height: 1.45;
  }
  .accent-bar {
    position: absolute; left: 22px; top: 108px;
    width: 10px; height: 56px;
    background: var(--brand-blue);
  }
  .person-name { color: var(--brand-blue); font-weight: 700; font-size: 20px; line-height: 1.2; }
  .person-role { font-style: italic; color: var(--muted); font-size: 14px; margin-bottom: 8px; }
  .address { margin-bottom: 8px; }
  .contact-line { display: flex; align-items: center; gap: 8px; }
  .contact-line svg { width: 13px; height: 13px; fill: var(--brand-blue); flex: none; }
  .services-title { color: var(--brand-blue); font-size: 16px; margin-top: 8px; }
  .services { list-style: none; font-size: 13px; }
  .services li::before {
    content: ""; display: inline-block; width: 5px; height: 5px; border-radius: 50%;
    background: var(--brand-blue); margin-right: 7px; vertical-align: middle;
  }
</style>
</head>
<body>
  <section class="card card-front" aria-label="Card front">
    <div class="wordmark">
      <span class="wordmark-dot"></span>
      <span class="wordmark-name">Ridgeline<br>Construction</span>
    </div>
  </section>

  <section class="card card-back" aria-label="Card back">
    <div class="wordmark">
      <span class="wordmark-dot"></span>
      <span class="wordmark-name">Ridgeline<br>Construction</span>
    </div>

    <span class="accent-bar"></span>
    <div class="contact">
      <p class="person-name">Tomas verbick</p>
      <p class="person-role">Project manager</p>
      <p class="address">41 barrow crescent kelworth<br>52917306224783</p>
      <p class="contact-line">
        <svg viewBox="0 0 16 16" aria-hidden="true"><path d="M3.5 1 6 3.5 4.8 5.6c.8 2 2.3 3.6 4.3 4.5l2-1.2 2.5 2.6-1.6 2.2C6.8 13.4 2.2 8.8 1.4 3.6z"/></svg>
        (03) 9418 6573
      </p>
      <p class="contact-line">
        <svg viewBox="0 0 16 16" aria-hidden="true"><path d="M1 3h14v10H1zM2.5 4.5v.4L8 9l5.5-4.1v-.4z"/></svg>
        Info@verbickgroup.com
      </p>
      <p class="contact-line">
        <svg viewBox="0 0 16 16" aria-hidden="true"><circle cx="8" cy="8" r="7"/></svg>
        www.verbickgroup.com
      </p>
      <p class="services-title">Our Services</p>
      <ul class="services">
        <li>Civil construction</li>
        <li>Construction (commercial &amp; industrial)</li>
      </ul>
    </div>
  </section>
</body>
</html>
```